Kerrawong Bowls Club - Hospitality Venue - Need a poster to advertise Drink Spcials

I am looking at promoting our drinks on special to promote via poster and social media. I have uploaded an example. Please change and make it original to our venue. I have added our club logos also.
Gullwind Harbour Ale Schooner $6.00
Redgum Tallow Shiraz $8.50
Copper Heron Stubbie $10.00
Bay Breeze Cocktail $10.00
Fenwick Pear Cider  $5.00
Post Mix Jug $10.00
Please mention in fine print at the bottom.
The Kerrawong Bowls Club practices the Responsible Service of Alcohol. No Members discount apply to these prices

Target Market(s)
Adults
Industry/Entity Type
Bar
Look and feel
Each slider illustrates characteristics of the customer's brand and the style your logo design should communicate.

```html
<!DOCTYPE html>
<html lang="en">
<head>
<meta charset="utf-8">
<title>Kerrawong Bowls Club – Drinks Specials</title>
<link href="https://fonts.googleapis.com/css2?family=Montserrat:wght@500;600;700;800&family=Great+Vibes&display=swap" rel="stylesheet">
<style>
  :root {
    --night: #141210;
    --amber: #f2b41c;
    --gold: #e8a317;
    --yellow: #ffe100;
    --card: rgba(205, 205, 210, 0.42);
    --ink: #111111;
    --white: #ffffff;
    --muted: #d8d8d8;
  }
  * { box-sizing: border-box; margin: 0; padding: 0; }
  html, body { width: 1200px; height: 2388px; overflow: hidden; background: var(--night); }
  body { font-family: "Montserrat", Arial, sans-serif; color: var(--white); }

  .poster { position: relative; width: 1200px; height: 2388px; overflow: hidden; }
  .bar-backdrop {
    position: absolute; inset: 0;
    background:
      radial-gradient(ellipse at 20% 30%, rgba(170, 110, 40, 0.45), transparent 55%),
      radial-gradient(ellipse at 85% 45%, rgba(140, 90, 35, 0.4), transparent 50%),
      radial-gradient(ellipse at 50% 85%, rgba(90, 60, 30, 0.5), transparent 60%),
      linear-gradient(180deg, #1d1712 0%, #2b2119 40%, #1a1511 100%);
  }

  .header { position: absolute; left: 0; top: 0; width: 100%; height: 600px; }
  .club-mark { position: absolute; left: 70px; top: 70px; display: flex; align-items: center; gap: 18px; }
  .club-mark__dot { width: 120px; height: 120px; border-radius: 50%; background: var(--amber); }
  .club-mark__name { font-weight: 700; font-size: 30px; line-height: 1.15; color: var(--white); width: 220px; }

  .title { position: absolute; right: 80px; top: 150px; text-align: right; }
  .title__main { font-weight: 800; font-size: 150px; letter-spacing: 6px; line-height: 1; color: var(--white); }
  .title__script { font-family: "Great Vibes", cursive; font-size: 170px; color: var(--gold); line-height: 0.9; margin-top: -10px; margin-right: 10px; }
  .title__rule { position: absolute; left: 360px; top: 400px; width: 760px; height: 6px; background: var(--amber); border-radius: 3px; }

  .menu-grid {
    position: absolute; left: 70px; top: 640px; width: 1060px;
    display: grid; grid-template-columns: repeat(3, 1fr); gap: 34px 30px;
  }
  .drink-card {
    height: 600px; background: var(--card); border-radius: 30px;
    display: flex; flex-direction: column; align-items: center; padding: 40px 24px 36px;
  }
  .drink-card__image { width: 180px; height: 330px; border-radius: 14px; }
  .drink-card__name {
    margin-top: 36px; font-weight: 700; font-size: 26px; line-height: 1.25;
    text-align: center; text-transform: uppercase; min-height: 66px; color: var(--white);
  }
  .drink-card__price {
    margin-top: auto; background: var(--white); color: var(--ink);
    font-weight: 800; font-size: 30px; padding: 8px 30px; border-radius: 8px;
  }
  .drink-card__price sup { font-size: 18px; }

  .img-beer { background: linear-gradient(180deg, #fbf3df 0%, #f0b53a 22%, #d98d12 100%); }
  .img-wine { background: linear-gradient(180deg, #5a1b1e, #2a0b0d); width: 110px; }
  .img-bourbon { background: linear-gradient(180deg, #3a2415, #8a5a2a 50%, #241509); width: 110px; }
  .img-cocktail { background: linear-gradient(180deg, #e83b52, #b2132d 55%, #f2f2f2); width: 150px; }
  .img-cider { background: linear-gradient(180deg, #dfe8a8, #b7cf3c 50%, #6a8a1e); width: 100px; }
  .img-jug { background: linear-gradient(180deg, #e9e4d8, #5a2c16 30%, #2e140a); width: 220px; }

  .footer { position: absolute; left: 0; top: 1980px; width: 100%; height: 408px; }
  .footer__web {
    position: absolute; left: 70px; top: 70px; width: 760px; height: 78px;
    background: var(--yellow); color: var(--ink); border-radius: 6px;
    font-weight: 700; font-size: 36px; display: flex; align-items: center; padding-left: 34px;
  }
  .footer__fineprint { position: absolute; left: 70px; top: 180px; width: 760px; font-size: 21px; line-height: 1.5; color: var(--muted); font-weight: 500; }
  .venue-mark {
    position: absolute; right: 70px; top: 50px; width: 260px; height: 260px;
    background: var(--white); border-radius: 8px;
    display: flex; flex-direction: column; align-items: center; justify-content: center; gap: 18px;
  }
  .venue-mark__dot { width: 64px; height: 64px; border-radius: 50%; background: #2a2a2a; }
  .venue-mark__name { font-weight: 600; font-size: 34px; letter-spacing: 6px; color: #2a2a2a; }
</style>
</head>
<body>
<main class="poster">
  <div class="bar-backdrop" role="img" aria-label="Softly blurred photo of a warmly lit bar with shelves of bottles"></div>

  <header class="header">
    <div class="club-mark">
      <span class="club-mark__dot"></span>
      <span class="club-mark__name">Kerrawong Bowls Club</span>
    </div>
    <div class="title__rule"></div>
    <div class="title">
      <h1 class="title__main">DRINKS</h1>
      <p class="title__script">specials</p>
    </div>
  </header>

  <section class="menu-grid">
    <article class="drink-card">
      <div class="drink-card__image img-beer" role="img" aria-label="Schooner glass of pale ale"></div>
      <h2 class="drink-card__name">Gullwind Harbour Ale Schooner</h2>
      <p class="drink-card__price"><sup>$</sup>6.00</p>
    </article>
    <article class="drink-card">
      <div class="drink-card__image img-wine" role="img" aria-label="Bottle of shiraz red wine"></div>
      <h2 class="drink-card__name">Redgum Tallow Shiraz Glass</h2>
      <p class="drink-card__price"><sup>$</sup>8.50</p>
    </article>
    <article class="drink-card">
      <div class="drink-card__image img-bourbon" role="img" aria-label="Bourbon and cola stubbie"></div>
      <h2 class="drink-card__name">Copper Heron Stubbie</h2>
      <p class="drink-card__price"><sup>$</sup>10.00</p>
    </article>
    <article class="drink-card">
      <div class="drink-card__image img-cocktail" role="img" aria-label="Red cocktail in a stemmed glass"></div>
      <h2 class="drink-card__name">Bay Breeze Cocktail</h2>
      <p class="drink-card__price"><sup>$</sup>10.00</p>
    </article>
    <article class="drink-card">
      <div class="drink-card__image img-cider" role="img" aria-label="Bottle of pear cider"></div>
      <h2 class="drink-card__name">Fenwick Pear Cider Stubbie</h2>
      <p class="drink-card__price"><sup>$</sup>5.00</p>
    </article>
    <article class="drink-card">
      <div class="drink-card__image img-jug" role="img" aria-label="Jug of cola with ice"></div>
      <h2 class="drink-card__name">Post Mix Jug</h2>
      <p class="drink-card__price"><sup>$</sup>10.00</p>
    </article>
  </section>

  <footer class="footer">
    <p class="footer__web">www.kerrawongbowls.com.au</p>
    <p class="footer__fineprint">*The Kerrawong Bowls Club practices the Responsible Service of Alcohol. No Members discount apply to these prices. Excludes function bars.</p>
    <div class="venue-mark">
      <span class="venue-mark__dot"></span>
      <span class="venue-mark__name">BELFRY</span>
    </div>
  </footer>
</main>
</body>
</html>
```